Business card design for new eCommerce site focusing on integrity and strong businsess tactics

We need a business card that will stand out and be memorable. Something with color that matches our company logo colors. Think high end version of Pactivo. There are 2 logos provided. The parent company is called Amber Ledge Partners and we are presenting a new and very exciting eCommerce site called BrightHarborTrade.example.

Target Market(s)

Our target markets are in the Activities, Food and Beverage, Health and Beauty

Industry/Entity Type

Marketing

Contact Information for Business Card

We have 4 members that need cards...I will provide all info to the winner of the design contest
Business Address is
4870 West 63rd Avenue, Suite C207
Phoenix AZ 85731

Font styles to use
Serif
Sans Serif

Colors

Designer to choose colors to be used in the design.

Requirements
Must have
• The card must be memorable...should be unique in design but must exude integrity and be playful .
• I have provided several colors or our parent company...please feel free to use which ever
Nice to have
• I will leave this up to you. Feel free to use other images of your choosing that wraps around our client.....Activities, Dining, Health, Beauty
Should not have
• just dont be boring

```html
<!DOCTYPE html>
<html lang="en">
<head>
<meta charset="utf-8">
<title>Keelwise.example – Business Card</title>
<link href="https://fonts.googleapis.com/css2?family=Roboto:wght@400;500;700&display=swap" rel="stylesheet">
<style>
  :root {
    --page-bg: #e4e5e3;
    --card-bg: #f3f4f2;
    --brand-blue: #2c5f96;
    --brand-deep: #1f4f86;
    --brand-stripe: #4a7fb8;
    --brand-green: #5aa83a;
    --text-dark: #3d3f42;
    --icon-grey: #44474b;
  }
  * { margin: 0; padding: 0; box-sizing: border-box; }
  html, body {
    width: 1200px; height: 969px; overflow: hidden;
    background: var(--page-bg);
    font-family: "Roboto", Arial, sans-serif;
  }
  .card {
    position: absolute; left: 100px; top: 200px;
    width: 1000px; height: 569px;
    background: var(--card-bg);
    border-radius: 22px; overflow: hidden;
    box-shadow: 0 10px 30px rgba(0,0,0,0.12);
  }
  .card-band { position: absolute; inset: 0; width: 1000px; height: 569px; }
  .brand { position: absolute; left: 95px; top: 62px; display: flex; align-items: center; gap: 16px; }
  .brand-dot { width: 46px; height: 46px; border-radius: 50%; background: var(--brand-blue); flex: none; }
  .brand-name { font-size: 42px; font-weight: 500; color: var(--brand-blue); line-height: 1; white-space: nowrap; }
  .brand-tagline {
    position: absolute; left: 157px; top: 120px;
    font-size: 20px; font-weight: 500; color: var(--text-dark); letter-spacing: 0.5px;
    white-space: nowrap;
  }
  .person { position: absolute; left: 64px; top: 222px; }
  .person-name { font-size: 38px; font-weight: 500; color: var(--brand-blue); letter-spacing: 0.5px; white-space: nowrap; }
  .person-title { font-size: 24px; font-weight: 500; color: var(--brand-green); margin-top: 2px; }
  .address {
    position: absolute; left: 64px; top: 314px;
    font-size: 26px; color: var(--text-dark); line-height: 33px; white-space: nowrap;
  }
  .contacts { position: absolute; left: 64px; top: 390px; list-style: none; }
  .contacts li {
    display: flex; align-items: center; gap: 16px;
    font-size: 24px; color: var(--text-dark); height: 32.5px; white-space: nowrap;
  }
  .contacts svg { width: 22px; height: 22px; fill: var(--icon-grey); flex: none; }
</style>
</head>
<body>
  <div class="card">
    <svg class="card-band" viewBox="0 0 1000 569" aria-hidden="true">
      <path d="M830 0 C 700 150, 800 330, 690 569 L 1000 569 L 1000 0 Z" fill="var(--brand-deep)"/>
      <path d="M905 0 C 800 160, 900 360, 790 569" fill="none" stroke="var(--brand-stripe)" stroke-width="14" opacity="0.6"/>
    </svg>

    <div class="brand">
      <span class="brand-dot"></span>
      <span class="brand-name">Keelwise.example</span>
    </div>
    <div class="brand-tagline">Leisure-Meals-Wellness-Style</div>

    <div class="person">
      <div class="person-name">DANA WHITFIELD</div>
      <div class="person-title">CEO/FOUNDER</div>
    </div>

    <div class="address">
      4870 West 63rd Avenue<br>
      Suite C207, Phoenix AZ 85731
    </div>

    <ul class="contacts">
      <li>
        <svg viewBox="0 0 24 24"><path d="M6.6 10.8a15 15 0 0 0 6.6 6.6l2.2-2.2c.3-.3.7-.4 1-.2 1.1.4 2.3.6 3.6.6.6 0 1 .4 1 1V20c0 .6-.4 1-1 1A17 17 0 0 1 3 4c0-.6.4-1 1-1h3.5c.6 0 1 .4 1 1 0 1.3.2 2.5.6 3.6.1.3 0 .7-.2 1z"/></svg>
        555 014 7720
      </li>
      <li>
        <svg viewBox="0 0 24 24"><path d="M7 1h10a2 2 0 0 1 2 2v18a2 2 0 0 1-2 2H7a2 2 0 0 1-2-2V3a2 2 0 0 1 2-2zm0 3v14h10V4zm5 15.5a1 1 0 1 0 0 2 1 1 0 0 0 0-2z"/></svg>
        555 019 3186
      </li>
      <li>
        <svg viewBox="0 0 24 24"><path d="M2 5h20v14H2zm2 2v.5l8 5 8-5V7zm0 3v7h16v-7l-8 5z"/></svg>
        dana@keelwise.example
      </li>
      <li>
        <svg viewBox="0 0 24 24"><path d="M12 2a10 10 0 1 0 0 20 10 10 0 0 0 0-20zm-1 17.9A8 8 0 0 1 4.2 10.2L9 15v1a2 2 0 0 0 2 2zm6.9-2.5A2 2 0 0 0 16 16h-1v-3a1 1 0 0 0-1-1H8v-2h2a1 1 0 0 0 1-1V7h2a2 2 0 0 0 2-2v-.4a8 8 0 0 1 2.9 12.8z"/></svg>
        www.keelwise.example
      </li>
    </ul>
  </div>
</body>
</html>
```